website design Investment Fund

I am looking for a custom website that will work on desktop computer, tablet device and a cellular device. I have attached the booklet so you can get an idea of the look we are going for. Would like to use the website eventually for crowdfunding. We like the ski racer and mountain climbing designs.

Target Market(s)

Financial Services

Industry/Entity Type

Financial Service

Coding

Coded - Design and coding required

Number of Pages Required

5+ page

Font styles to use
Sans Serif

Requirements
Must have
• Must be viewable on a cell phone and tablet and desktop
Nice to have
• Contact us form

```html
<!DOCTYPE html>
<html lang="en">
<head>
<meta charset="utf-8">
<title>Alder Ridge Capital II — Secured Income Fund</title>
<link href="https://fonts.googleapis.com/css2?family=Montserrat:wght@500;600;700;800;900&family=Raleway:wght@400;500;600;700&display=swap" rel="stylesheet">
<style>
:root{
  --red:#e8222a;
  --blue:#1d4fa0;
  --navy:#0b0d1f;
  --ink:#2b2b2b;
  --grey:#6b6b6b;
  --soft:#f6f6f7;
  --white:#ffffff;
}
*{margin:0;padding:0;box-sizing:border-box}
html,body{width:1200px;height:4392px;overflow:hidden}
body{position:relative;background:var(--white);font-family:"Raleway",sans-serif;color:var(--ink)}
.abs{position:absolute}
.heading{font-family:"Montserrat",sans-serif}
.snow-bg{left:0;top:0;width:1200px;height:2290px;background:linear-gradient(180deg,#c9ced6 0%,#e9ecf0 18%,#f4f5f7 30%,#e4e7ec 55%,#eef0f3 75%,#f3f4f6 100%)}
.mountain{left:250px;top:90px;width:500px;height:520px;background:radial-gradient(ellipse at 50% 40%,#8d939c 0%,#b8bdc5 45%,rgba(232,234,238,0) 75%)}
.team-bg{left:0;top:3150px;width:1200px;height:800px;background:var(--soft)}
/* header */
.header{left:0;top:0;width:1200px;height:84px;background:rgba(255,255,255,.92)}
.social-dot{width:11px;height:11px;border-radius:50%;background:var(--blue);top:41px}
.divider{left:222px;top:22px;width:1px;height:50px;background:#d9d9d9}
.nav a{position:absolute;top:39px;font-size:12px;color:#333;text-decoration:none;font-family:"Raleway",sans-serif;font-weight:500}
.nav a.active{color:var(--red)}
.brand{left:470px;top:94px;width:202px;text-align:center}
.brand-mark{width:54px;height:54px;background:var(--blue);margin:0 auto 10px;position:relative;top:-82px}
.brand-name{font-family:"Montserrat",sans-serif;font-weight:700;font-size:17px;color:var(--blue);letter-spacing:.5px;position:relative;top:-64px}
.brand-sub{font-family:"Montserrat",sans-serif;font-weight:700;font-size:8px;color:var(--blue);letter-spacing:.5px;position:relative;top:-64px}
.btn{display:inline-flex;align-items:center;height:42px;border-radius:21px;background:var(--white);box-shadow:0 2px 8px rgba(0,0,0,.15)}
.btn span{display:inline-flex;align-items:center;justify-content:center;height:42px;padding:0 24px;border-radius:21px;background:var(--red);color:#fff;font-family:"Montserrat",sans-serif;font-weight:600;font-size:13px}
.btn svg{margin:0 12px 0 10px}
/* hero */
.hero-photo{left:80px;top:175px;width:330px;height:390px;background:radial-gradient(ellipse at 45% 45%,#c43b36 0%,#8c4a4d 30%,#5a8f98 55%,rgba(225,228,233,0) 78%)}
.hero-title{left:730px;top:212px;font-family:"Montserrat",sans-serif;font-weight:900;line-height:.95}
.hero-title .blue{color:var(--blue);font-size:60px;display:block}
.hero-title .red{color:var(--red);font-size:76px;display:block}
.hero-sub{left:730px;top:410px;font-family:"Montserrat",sans-serif;font-weight:600;color:#222}
.hero-sub .s1{font-size:14px;display:block}
.hero-sub .s2{font-size:21px;display:block;margin-top:6px}
/* company */
.company{left:94px;top:655px;width:1012px;height:482px;background:var(--white);text-align:center;padding:58px 80px 0}
.company h1{font-family:"Montserrat",sans-serif;font-weight:700;font-size:60px;color:#2b2b2b;line-height:1}
.company h2{font-family:"Raleway",sans-serif;font-weight:500;font-size:33px;letter-spacing:4px;color:#333;margin-top:16px}
.company p{font-size:11.5px;line-height:19px;color:var(--grey);margin-top:14px}
.company .btn{margin-top:30px}
/* feature blocks */
.photo{background:linear-gradient(135deg,#dcd6d0,#b7aea6)}
.frame{border:9px solid var(--red)}
.feature-title{font-family:"Montserrat",sans-serif;font-weight:700;font-size:34px;line-height:38px;color:#2b2b2b}
.feature-text{font-size:11.5px;line-height:19px;color:#444}
/* accredited */
.acc-title{font-family:"Montserrat",sans-serif;font-weight:600;font-size:34px;color:#2b2b2b}
.acc-sub{font-family:"Montserrat",sans-serif;font-weight:700;font-size:29px;line-height:34px;color:var(--blue)}
.acc-series{font-family:"Montserrat",sans-serif;font-weight:600;font-size:22px;color:#222}
.acc-series em{font-style:normal;color:var(--red);font-weight:500}
.acc-rate{font-size:14px;color:#333}
/* team */
.team-title{left:0;width:1200px;text-align:center}
.team-title h3{font-family:"Montserrat",sans-serif;font-weight:700;font-size:35px;color:#2b2b2b}
.team-title p{font-family:"Raleway",sans-serif;font-size:28px;color:#555;margin-top:6px;letter-spacing:.5px}
.portrait{top:3356px;height:254px;background:linear-gradient(180deg,#9a9a9a,#4a4a4a)}
.portrait.selected{border:2px solid #6f9bd8;background:linear-gradient(180deg,#cfa58c,#7b5a4a)}
.bio{left:94px;top:3643px;width:1020px;height:217px;background:var(--white);box-shadow:0 2px 10px rgba(0,0,0,.06);padding:32px 24px}
.bio h4{font-family:"Montserrat",sans-serif;font-weight:600;font-size:18px;color:#222}
.bio .role{font-size:15px;color:#555;letter-spacing:1px;margin-top:2px}
.bio p{font-size:10.5px;line-height:18px;color:#555;margin-top:8px;width:920px}
.bio .btn{margin-top:14px}
/* footer */
.footer{left:0;top:3880px;width:1200px;height:512px}
.footer-col{color:#fff}
.footer-col h5{font-family:"Montserrat",sans-serif;font-weight:600;font-size:16px;margin-bottom:18px}
.footer-col li{list-style:none;font-size:11px;line-height:22px;color:#ddd}
.footer-col li::before{content:"›";margin-right:8px}
.contact-row{display:flex;gap:12px;font-size:10.5px;line-height:18px;color:#ddd;margin-bottom:6px}
.footer-brand{font-family:"Montserrat",sans-serif;font-weight:700;font-size:15px;color:#fff;display:flex;align-items:center;gap:10px}
.footer-brand i{width:30px;height:30px;background:var(--blue);display:block}
.footer-small{font-size:10.5px;line-height:17px;color:#ddd}
.social-circle{width:33px;height:33px;border-radius:50%;background:#fff;display:inline-block;margin-right:8px}
.email-input{left:873px;top:4178px;width:233px;height:40px;border:1px solid #666;border-radius:20px;color:#777;font-size:11px;padding:13px 24px}
.copyright{left:0;top:4360px;width:1200px;height:32px;background:#05060f;color:#aaa;font-size:9.5px;text-align:center;line-height:32px}
</style>
</head>
<body>

<div class="abs snow-bg" role="img" aria-label="Snowy mountain landscape backdrop"></div>
<div class="abs mountain" role="img" aria-label="Snow-covered mountain peak"></div>
<div class="abs team-bg"></div>

<!-- header -->
<header class="abs header">
  <span class="abs social-dot" style="left:92px"></span>
  <span class="abs social-dot" style="left:118px"></span>
  <span class="abs social-dot" style="left:152px"></span>
  <div class="abs divider"></div>
  <nav class="nav">
    <a class="active" style="left:258px">Home</a>
    <a style="left:331px">About Us</a>
    <a style="left:421px">Travel</a>
    <a style="left:664px">Gallary</a>
    <a style="left:742px">Testimonial</a>
    <a style="left:845px">Contact Us</a>
  </nav>
  <div class="abs" style="left:965px;top:26px">
    <div class="btn"><span>Read More</span><svg width="12" height="8" viewBox="0 0 12 8"><path d="M1 1l5 5 5-5" fill="none" stroke="#222" stroke-width="2"/></svg></div>
  </div>
</header>
<div class="abs brand">
  <div class="brand-mark"></div>
  <div class="brand-name">ALDER RIDGE CAPITAL II</div>
  <div class="brand-sub">SECURED INCOME FUND</div>
</div>

<!-- hero -->
<div class="abs hero-photo" role="img" aria-label="Skier in a red jacket carving through powder snow"></div>
<svg class="abs" style="left:560px;top:175px" width="140" height="300"><line x1="6" y1="4" x2="130" y2="295" stroke="#e8222a" stroke-width="6"/></svg>
<div class="abs hero-title">
  <span class="blue">TOTALLY</span>
  <span class="blue">COMMITTED</span>
  <span class="red">FOCUSED</span>
</div>
<div class="abs hero-sub">
  <span class="s1">ON CAPITAL PRESERVATION AND UNINTERRUPTED</span>
  <span class="s2">INCOME FOR OUR INVESTORS</span>
</div>

<!-- company -->
<section class="abs company">
  <h1>THE COMPANY—</h1>
  <h2>Arizona's Elite Boutique Lender</h2>
  <p style="margin-top:22px">Alder Ridge Funding &amp; Investment, Inc. is a privately held mortgage lender, asset management and advisory firm headquartered in Scottsdale, Arizona which specializes in fast financing for debt,equity, mezzanine and land bank on real estate projects in the $100,000 to $50,000,000 range. As a highly reputable, successful and growth-focused company with decades of experience acrossthe entire spectrum of real estate financing through Arizona, the Southwest United States and Mexico.</p>
  <p>At Alder Ridge, we've created an exceptional business focused on delivering privately funded financing to a wide range of clients. Our proven diligence, impeccable operating standards and expertisehelp to ensure that the funding process will run more rapidly and reliably than any other company in that market.</p>
  <p>We're proud of the incomparable personal service and years of combined experience we bring to each and every loan negotiation which enables us to mitigate risk and bring our clients and partners a fast and efficient closing process.</p>
  <div class="btn"><span>Read More</span><svg width="12" height="8" viewBox="0 0 12 8"><path d="M1 1l5 5 5-5" fill="none" stroke="#222" stroke-width="2"/></svg></div>
</section>

<!-- boutique fund -->
<div class="abs photo" style="left:94px;top:1262px;width:436px;height:424px;background:linear-gradient(135deg,#f1ece6,#d9cfc6 60%,#b98e74)" role="img" aria-label="Woman browsing shoes on a boutique shelf"></div>
<div class="abs frame" style="left:581px;top:1280px;width:525px;height:376px;border-left:none"></div>
<div class="abs" style="left:581px;top:1358px;width:480px">
  <div class="feature-title">THE BOUTIQUE FUND INVESTORS ARE LOOKING FOR</div>
  <p class="feature-text" style="margin-top:18px">As an ELITE BOUTIQUE, full-service, and highly selective firm, we only present our investors deals with highly qualified borrowers and properties with loan to value ratios (LTV) not to exceed 65%-70%. Simply put, we only fund deals with enough equity to allow for a Real Estate market change. All loans are short term so we can easily monitor changes in valuation and market conditions.</p>
</div>

<!-- investment strategy -->
<div class="abs frame" style="left:94px;top:1808px;width:525px;height:375px;border-right:none"></div>
<div class="abs" style="left:143px;top:1925px;width:470px">
  <div class="feature-title">INVESTMENT STRATEGY:</div>
  <p class="feature-text" style="margin-top:12px">The Fund Managers have decades of experience in private money lending as well as real estate investment, property and asset management, construction, and development. In order to produce the desired investor yields, the Fund Managers will utilize their extensive relationships in the marketplace to make a diversified series of investments in secured loans, equity joint ventures, and select value-add real estate investments.</p>
</div>
<div class="abs photo" style="left:670px;top:1782px;width:436px;height:424px;background:linear-gradient(135deg,#5a4a3c,#c9c3bd 45%,#2f5f9e 70%,#3a3a3a)" role="img" aria-label="Laptop showing investment charts on a wooden desk"></div>

<!-- blue curve -->
<svg class="abs" style="left:0;top:2255px" width="1200" height="60"><path d="M0 30 Q600 -10 1200 30 L1200 60 L0 60Z" fill="#fff"/><path d="M0 30 Q600 -10 1200 30" fill="none" stroke="#1d4fa0" stroke-width="5"/></svg>

<!-- accredited 1 -->
<div class="abs photo" style="left:94px;top:2325px;width:440px;height:315px;background:linear-gradient(135deg,#e4e6ea,#8d96a8 55%,#2c3850)" role="img" aria-label="Hand stamping a document at a desk"></div>
<div class="abs" style="left:573px;top:2383px">
  <div class="acc-title">ACCREDITED INVESTORS ONLY</div>
  <div class="acc-sub" style="margin-top:18px">MINIMUM INVESTMENT<br>REQUIREMENTS</div>
  <div class="acc-series" style="margin-top:24px">SERIES A &nbsp; <em>$50,000 &nbsp;- &nbsp;$249,999</em></div>
  <div class="acc-rate" style="margin-top:10px">Rate of the return sries a <b>7%</b> per annum term <b>24</b> Month</div>
</div>

<!-- accredited 2 -->
<div class="abs" style="left:98px;top:2792px">
  <div class="acc-title">ACCREDITED INVESTORS ONLY</div>
  <div class="acc-sub" style="margin-top:18px">MINIMUM INVESTMENT<br>REQUIREMENTS</div>
  <div class="acc-series" style="margin-top:22px">SERIES &nbsp; &nbsp; &nbsp;B <em>$250,000.00</em></div>
  <div class="acc-rate" style="margin-top:10px">Rate of the return sries a 7% per annum term <b>24</b> Month</div>
</div>
<div class="abs photo" style="left:662px;top:2745px;width:440px;height:315px;background:linear-gradient(135deg,#cfc9c4,#eef0f3 50%,#9aa3b3)" role="img" aria-label="Hands holding a tablet with a financial dashboard"></div>

<!-- blue curve -->
<svg class="abs" style="left:0;top:3110px" width="1200" height="60"><path d="M0 5 Q600 60 1200 5 L1200 60 L0 60Z" fill="#f6f6f7"/><path d="M0 5 Q600 60 1200 5" fill="none" stroke="#1d4fa0" stroke-width="5"/></svg>

<!-- team -->
<div class="abs team-title" style="top:3242px">
  <h3>OUR TEAM</h3>
  <p>FOUNDING MEMBERS AND FUND MANAGERS</p>
</div>
<div class="abs portrait selected" style="left:94px;width:294px" role="img" aria-label="Portrait of the founder"></div>
<div class="abs portrait" style="left:402px;width:226px" role="img" aria-label="Portrait of a fund manager"></div>
<div class="abs portrait" style="left:642px;width:226px" role="img" aria-label="Portrait of a fund manager"></div>
<div class="abs portrait" style="left:882px;width:226px" role="img" aria-label="Portrait of a fund manager"></div>
<svg class="abs" style="left:222px;top:3625px" width="36" height="19"><path d="M0 19 L18 0 L36 19Z" fill="#fff"/></svg>
<section class="abs bio">
  <h4>DANIEL R. HALE</h4>
  <div class="role">Founder and &nbsp;Fund Manager</div>
  <p>Daniel is a real estate development and finance entrepreneur and executive with over 37 years of entrepreneur experience. As the Founder, Chairman and CEO of Alder Ridge Funding and Investments, Inc. a privately held mortgage lender and advisory firm headquartered in Scottsdale Arizona. In addition to his real estate lending, Daniel has joint ventured development of residential and commercial properties in the Phoenix metropolitan area along with building $1 million condominium development in Costa</p>
  <div class="btn"><span>Read More</span><svg width="12" height="8" viewBox="0 0 12 8"><path d="M1 1l5 5 5-5" fill="none" stroke="#222" stroke-width="2"/></svg></div>
</section>

<!-- footer -->
<svg class="abs footer" width="1200" height="512" viewBox="0 0 1200 512">
  <path d="M0 0 Q120 90 300 70 Q480 50 600 110 Q760 180 900 80 Q1050 -10 1200 30 L1200 512 L0 512Z" fill="#0b0d1f"/>
  <path d="M0 0 Q120 90 300 70 Q480 50 600 110 Q760 180 900 80 Q1050 -10 1200 30" fill="none" stroke="#e8222a" stroke-width="6"/>
</svg>

<div class="abs footer-col" style="left:94px;top:4100px;width:310px">
  <div class="footer-brand"><i></i>ALDER RIDGE CAPITAL II</div>
  <p class="footer-small" style="margin-top:28px">2200 N. Canyon View Rd Suite 9<br>Scottsdale, AZ 85255</p>
  <div style="height:1px;background:#555;margin:8px 0 10px;width:310px"></div>
  <p class="footer-small">This document is intended as a summary of certain information contained in the ALDER RIDGE CAPITAL II SECURED INCOME FUND.</p>
  <div style="margin-top:18px"><span class="social-circle"></span><span class="social-circle"></span><span class="social-circle"></span></div>
</div>

<div class="abs footer-col" style="left:457px;top:4118px">
  <h5>Site Map</h5>
  <ul><li>Home</li><li>About Us</li><li>Travel</li><li>Gallary</li><li>Testimonial</li><li>Contact Us</li></ul>
</div>

<div class="abs footer-col" style="left:651px;top:4118px">
  <h5>Contact Us</h5>
  <div class="contact-row"><svg width="10" height="16"><path d="M8 1 Q1 8 8 15" fill="none" stroke="#fff" stroke-width="2.5"/></svg><span>DANIEL R. HALE<br>480-555-0142</span></div>
  <div class="contact-row"><svg width="10" height="16"><path d="M8 1 Q1 8 8 15" fill="none" stroke="#fff" stroke-width="2.5"/></svg><span>LAURA BENNETT<br>602-555-0187</span></div>
  <div class="contact-row"><svg width="10" height="16"><path d="M8 1 Q1 8 8 15" fill="none" stroke="#fff" stroke-width="2.5"/></svg><span>DANIEL R. HALE<br>480-555-0142</span></div>
  <div class="contact-row"><svg width="10" height="16"><path d="M8 1 Q1 8 8 15" fill="none" stroke="#fff" stroke-width="2.5"/></svg><span>LAURA BENNETT<br>602-555-0187</span></div>
</div>

<div class="abs footer-col" style="left:872px;top:4118px"><h5>Newsleeter</h5></div>
<div class="abs email-input">Enater Your Email</div>
<div class="abs" style="left:877px;top:4236px">
  <div class="btn"><span>Subscribe</span><svg width="12" height="8" viewBox="0 0 12 8"><path d="M1 1l5 5 5-5" fill="none" stroke="#222" stroke-width="2"/></svg></div>
</div>

<div class="abs copyright">© CopyRight 2019 ALDER RIDGE . Allright Reserved</div>

</body>
</html>
```